Flyer informing about the activities of people in action

Leute im Wandel (www.leuteimwandel.ch) offers coaching, medation, support for traumatized people and conflict and crisis intervention. The flyer should inform about the activities in a plain and simple way (see logo on the homepage).

Target Market(s)

Adults who live in Switzerland or Germany

Requirements
Must have
• - simple flyer, the design is based on my logo. Brief information about my offer, reference to my homepage www.leuteimwandel.
- 2-sided: on the first page - fire circle with text (see homepage - Home), on the back - offer with logo
- possibly a square flyer

Should not have
• no photos

```html
<!DOCTYPE html>
<html lang="de">
<head>
<meta charset="utf-8">
<title>Leute im Wandel – Flyer</title>
<link rel="stylesheet" href="https://fonts.googleapis.com/css2?family=Raleway:wght@400;500;600;700&display=swap">
<style>
  :root {
    --stage: #ebebef;
    --paper: #ffffff;
    --gold: #9a7a2e;
    --gold-text: #a8874a;
    --ink: #2b2b2b;
    --blue: #2c3f92;
    --glow: 246,217,198;
  }
  * { box-sizing: border-box; margin: 0; padding: 0; }
  html, body { width: 960px; height: 1200px; overflow: hidden; }
  body {
    background: var(--stage);
    font-family: "Raleway", Arial, sans-serif;
    position: relative;
  }
  .card {
    position: absolute;
    left: 210px;
    width: 540px;
    height: 540px;
    box-shadow: 0 4px 14px rgba(0,0,0,.22);
    overflow: hidden;
  }
  .card--front { top: 30px; background: var(--paper); color: var(--ink); }
  .card--back { top: 630px; background: var(--gold); color: #fff; }

  /* Front */
  .front__glow {
    position: absolute;
    left: 80px; top: 90px;
    width: 380px; height: 380px;
    border-radius: 50%;
    background: radial-gradient(circle, rgba(var(--glow),.55) 0%, rgba(var(--glow),.35) 55%, rgba(var(--glow),0) 72%);
  }
  .front__intro { position: absolute; left: 34px; top: 34px; }
  .front__lead { font-size: 22px; font-weight: 500; margin-bottom: 6px; }
  .front__intro p { font-size: 17px; line-height: 1.3; }
  .front__brand {
    position: absolute;
    left: 40px; right: 40px; top: 215px;
    display: flex;
    align-items: center;
    justify-content: center;
    gap: 16px;
  }
  .front__ring {
    flex: none;
    width: 58px; height: 58px;
    border: 4px solid var(--gold-text);
    border-radius: 50%;
  }
  .front__name {
    font-size: 44px;
    font-weight: 600;
    color: var(--gold-text);
    white-space: nowrap;
  }
  .front__claim {
    position: absolute;
    right: 34px; top: 395px;
    text-align: right;
  }
  .front__claim strong { display: block; font-size: 20px; font-weight: 500; margin-bottom: 4px; }
  .front__claim p { font-size: 16px; line-height: 1.3; }
  .front__url {
    position: absolute;
    left: 0; right: 0; bottom: 36px;
    text-align: center;
    font-size: 14px; font-weight: 600;
    color: var(--gold-text);
  }

  /* Back */
  .back__frame {
    position: absolute;
    left: 30px; right: 30px; top: 112px; bottom: 30px;
    border: 1.5px solid rgba(255,255,255,.9);
  }
  .back__brand {
    position: absolute;
    left: 50%; top: 26px;
    transform: translateX(-50%);
    display: flex; align-items: center; gap: 10px;
    white-space: nowrap;
  }
  .back__dot { width: 30px; height: 30px; border: 2px solid #fff; border-radius: 50%; }
  .back__name { font-size: 22px; font-weight: 600; color: #fff; }
  .back__content { position: absolute; left: 48px; right: 48px; top: 150px; }
  .back__intro { text-align: center; font-size: 16px; margin-bottom: 4px; }
  .back__promise { text-align: center; font-size: 17px; font-weight: 600; margin-bottom: 22px; }
  .offer { margin-bottom: 16px; }
  .offer h2 { font-size: 14.5px; font-weight: 700; margin-bottom: 3px; }
  .offer p { font-size: 13px; line-height: 1.4; }
  .back__url {
    position: absolute; left: 0; right: 0; bottom: 40px;
    text-align: center; font-size: 17px; font-weight: 700;
    color: var(--blue);
  }
</style>
</head>
<body>
  <section class="card card--front" aria-label="Flyer Vorderseite">
    <div class="front__glow" role="img" aria-label="Zarte Feuerkreis-Dekoration in Pfirsichtönen"></div>
    <div class="front__intro">
      <h1 class="front__lead">Sie möchten</h1>
      <p>Ihre belastende Situation lösen.<br>Ihre wichtigen Fragen klären.</p>
    </div>
    <div class="front__brand">
      <span class="front__ring"></span>
      <span class="front__name">Leute im Wandel</span>
    </div>
    <div class="front__claim">
      <strong>leichter weiterkommen</strong>
      <p>in der frustrierenden Zusammenarbeit<br>oder Ihrem mühsamen (Zusammen-)Leben.</p>
    </div>
    <div class="front__url">www.leuteimwandel.ch</div>
  </section>

  <section class="card card--back" aria-label="Flyer Rückseite">
    <div class="back__frame"></div>
    <div class="back__brand">
      <span class="back__dot"></span>
      <span class="back__name">Leute im Wandel</span>
    </div>
    <div class="back__content">
      <p class="back__intro">Ich begleite Sie und bringe Ihnen</p>
      <p class="back__promise">Orientierung, Klarheit und Unterstützung.</p>
      <div class="offer">
        <h2>COACHING</h2>
        <p>Manchmal braucht man ein Gegenüber zum Klären der eigenen Situation oder beim Entdecken neuer Sichtweisen und Handlungsmöglichkeiten.</p>
      </div>
      <div class="offer">
        <h2>MEDIATION</h2>
        <p>Gewisse Konflikte können Sie nicht mehr selber lösen. Wenige Worte entzünden einen erbitterten Streit oder erzeugen eisige Stille.</p>
      </div>
      <div class="offer">
        <h2>BEGLEITUNG VON TRAUMATISIERTEN MENSCHEN</h2>
        <p>Ihr Leben fühlt sich oft schwer, bedrückend und freudlos an. Erfolglos haben Sie probiert, sich von dieser Kontakt- und Perspektivlosigkeit zu befreien.</p>
      </div>
    </div>
    <div class="back__url">www.leuteimwandel.ch</div>
  </section>
</body>
</html>
```